BRTL web site redesign

Coastal Linkage Engineering service (BRTL) is a diverse technology company specialising in design and installation of fibre optics, network convergence and building services, for commercial clients in Australia, we required a new design of our website to attract new clients, generate sales leads, and provide information about our services to the market. The site and should have a new technology look and feel and be designed in word press. our branding colour is blue.

Target Market(s)

New developments, Construction organisations, Commercial end users, IT managers, Consultants.

Industry/Entity Type

It Company

Number of Pages Required

5+ page

Font styles to use
Sans Serif

Colors
0292cd
3176b5

Requirements
Must have
• key pages.
• Home page with some sizzle, automated pictures running through, I like the look of this competitor website http://www.gleamwirex.com.au/ good clean menus and easy to navigate.
• Services page our key services are Fibre optics, Security, Building services,Electrical. I would like the same page layout (Design) for all our services, with a find out more link on each page, manly picture driven with text around our key messaging.
• About us page with space for company profile and directors pictures, bio and contact information.
• Certifications / Accreditations page with have over 20 certifications on different products from suppliers, and a number of licences from governing bodies.
• Current and past projects page with case studies and customer outcomes
• Contact us page with options around what services they require more information on, please keep in mind the site is around generating sales Leeds and being seen as an industry expert.
Nice to have
• RSS feeds, Linked in link, to be placed within the design, Consistent BRTL branding,Same colour blue as our logo Document library for education information, white papers, presentations etc,
• a new technology look and feel, mobile friendly.
Should not have
• boring layout, move away from our cuurent website http://www.brtlgroup.com.au/
• no e eCommerce store required.

```html
<!DOCTYPE html>
<html lang="en">
<head>
<meta charset="utf-8">
<title>BRTL — Coastal Linkage Engineering service</title>
<link rel="stylesheet" href="https://fonts.googleapis.com/css2?family=Lato:wght@400;700&family=PT+Sans:wght@400;700&family=Raleway:wght@400;600&display=swap">
<style>
:root{
  --brand:#0a78b5;
  --brand-dark:#06598a;
  --brand-light:#2fa6dd;
  --ink:#333;
  --muted:#555;
  --page-bg:#ebe8df;
  --white:#fff;
  --field-border:#cfd8de;
}
*{box-sizing:border-box;margin:0;padding:0}
html,body{width:1200px;height:2274px;overflow:hidden}
body{background:var(--page-bg);font-family:"Lato",sans-serif;color:var(--ink);position:relative}
.abs{position:absolute}
.page{left:97px;top:18px;width:1006px;height:2280px;background:var(--white);border:2px solid #d2d0ca;border-radius:14px 14px 0 0}

/* top bar */
.topbar{left:125px;top:33px;width:950px;height:20px;font-size:11px;color:var(--brand);display:flex;align-items:center}
.topbar .item{display:flex;align-items:center;gap:6px;margin-right:40px}
.topbar svg{fill:var(--brand)}
.social{position:absolute;right:0;top:3px;display:flex;gap:8px}
.social span{width:11px;height:11px;border-radius:50%;background:var(--brand)}

/* header band */
.header{left:32px;top:61px;width:1138px;height:97px;background:var(--brand);border-radius:18px}
.header-fold-l{left:32px;top:30px;width:70px;height:40px;background:var(--brand-dark);border-radius:14px 0 0 14px}
.header-fold-r{left:1100px;top:150px;width:70px;height:40px;background:var(--brand-dark);border-radius:0 0 14px 0}
.logo{left:125px;top:73px;height:76px;display:flex;align-items:center;gap:10px;font-family:"Lato",sans-serif;font-weight:700;font-size:46px;color:var(--white);letter-spacing:2px}
.logo i{width:18px;height:18px;background:var(--white);display:block}
.nav{right:120px;top:96px;display:flex;align-items:center;gap:18px;font-size:13.5px;color:var(--white)}
.nav a{color:inherit;text-decoration:none;padding:6px 6px}
.nav a.boxed{background:var(--white);color:var(--brand);padding:7px 10px}
.dropdown{left:577px;top:134px;width:124px;height:79px;background:var(--white);padding:6px 6px;font-size:10px;font-weight:700;color:var(--brand)}
.dropdown div{padding:6px 8px;border-bottom:1px solid #e5eef3}
.dropdown div.on{background:var(--brand);color:var(--white);border:0}

/* hero */
.hero{left:97px;top:158px;width:1006px;height:419px;background:linear-gradient(120deg,#1f2a33 0%,#3f5361 40%,#2c7fae 70%,#1a2026 100%)}
.hero-shadow{left:150px;top:577px;width:900px;height:20px;background:radial-gradient(ellipse at top,rgba(0,0,0,.25),transparent 70%)}
.caption{left:185px;top:293px;width:552px;height:132px;background:rgba(0,0,0,.72);padding:22px 25px;color:var(--white)}
.caption h1{font-family:"Raleway",sans-serif;font-weight:400;font-size:24px;margin-bottom:14px}
.caption p{font-family:"Raleway",sans-serif;font-size:14px;line-height:18px}
.btn-light{display:flex;align-items:center;justify-content:center;background:linear-gradient(#fff,#cfe7f3);color:var(--brand);font-weight:700;font-size:12px;border-radius:3px;box-shadow:0 2px 3px rgba(0,0,0,.2)}
.read-more{left:184px;top:436px;width:136px;height:39px;font-size:13px}
.arrow{top:334px;width:55px;height:49px;background:var(--brand);display:flex;align-items:center;justify-content:center}

/* section titles */
.title{left:97px;width:1006px;display:flex;align-items:center;justify-content:center;gap:10px;font-family:"PT Sans",sans-serif;font-size:37px;color:var(--brand)}
.title .rule{width:95px;height:2px;background:currentColor;position:relative}
.title .rule::after{content:"";position:absolute;top:-4px;width:8px;height:8px;background:currentColor;transform:rotate(45deg)}
.title .rule.l::after{right:-4px}
.title .rule.r::after{left:-4px}
.title.on-blue{color:var(--white)}

/* about */
.about-photo{left:125px;top:670px;width:299px;height:245px;background:radial-gradient(circle at 50% 55%,#bff0ff 0%,#1ca4dd 30%,#06306a 90%)}
.about-text{left:451px;top:665px;width:625px;font-size:11.6px;line-height:16.5px;color:var(--ink);text-align:justify}
.about-text p{margin-bottom:16px}
.btn-blue{display:flex;align-items:center;justify-content:center;background:linear-gradient(#5ac3ee,#0a78b5);color:var(--white);font-weight:700;font-size:11px;border-radius:3px}
.learn-more{left:451px;top:878px;width:137px;height:37px}

/* services */
.services{left:125px;top:949px;width:950px;height:403px;background:var(--brand)}
.service{top:1028px;width:200px;text-align:center;color:var(--white)}
.service .disc{width:186px;height:186px;border-radius:50%;border:2px solid var(--white);margin:0 auto 26px;display:flex;align-items:center;justify-content:center}
.service h3{font-family:"PT Sans",sans-serif;font-weight:400;font-size:21px;margin-bottom:6px}
.service p{font-size:11.3px;line-height:15px;text-align:justify;height:45px;overflow:hidden}

/* projects */
.filters{left:413px;top:1432px;display:flex;gap:20px}
.filters span{height:34px;display:flex;align-items:center;justify-content:center;background:linear-gradient(#5ac3ee,#0a78b5);color:#d9f2ff;font-size:14px;border-radius:3px;position:relative}
.filters span.on::after{content:"";position:absolute;bottom:-7px;left:50%;margin-left:-7px;border:7px solid transparent;border-top-color:var(--brand);border-bottom:0}
.project{top:1501px;width:299px}
.project .shot{height:188px;border-radius:3px;position:relative}
.project h3{font-family:"Lato",sans-serif;font-weight:400;font-size:15px;color:var(--brand);margin:18px 0 8px}
.project p{font-size:11.2px;line-height:15.2px;color:var(--ink);height:76px;overflow:hidden}
.overlay{position:absolute;left:18px;top:18px;width:263px;height:152px;background:rgba(10,120,181,.85);display:flex;align-items:center;justify-content:center}

/* footer */
.footer{left:125px;top:1850px;width:950px;height:430px;background:var(--brand);color:var(--white)}
.footer h4{position:absolute;top:23px;font-family:"PT Sans",sans-serif;font-weight:400;font-size:21px}
.contact-note{position:absolute;left:15px;top:62px;font-size:12px}
.field{position:absolute;background:var(--white);border:1px solid var(--field-border);font-size:10.5px;color:#666;padding:7px 6px}
.submit{position:absolute;left:16px;top:293px;width:119px;height:35px;font-size:11px}
.links{position:absolute;top:60px;width:140px;font-size:12.5px}
.links div{padding:8px 0 6px;border-bottom:1px solid rgba(255,255,255,.25);height:38px}
.links.wide{width:215px}
.tweets{position:absolute;left:729px;top:62px;width:200px}
.tweet{display:flex;gap:8px;margin-bottom:18px;font-size:11px;line-height:15px}
.tweet i{flex:none;width:16px;height:16px;border-radius:50%;background:var(--white);margin-top:2px}
.tweet small{display:block;font-size:10.5px;margin-top:4px;padding-bottom:6px;border-bottom:1px solid rgba(255,255,255,.25)}
.footer-rule{position:absolute;left:15px;top:356px;width:920px;height:1px;background:rgba(255,255,255,.25)}
.copyright{position:absolute;left:0;top:380px;width:950px;text-align:center;font-size:10.5px;color:#6cb6de}
</style>
</head>
<body>

<div class="abs page"></div>

<div class="abs header-fold-l"></div>
<div class="abs header-fold-r"></div>

<div class="abs topbar">
  <div class="item">
    <svg width="10" height="10" viewBox="0 0 24 24"><path d="M6.6 10.8a15 15 0 0 0 6.6 6.6l2.2-2.2a1 1 0 0 1 1-.25 11.4 11.4 0 0 0 3.6.6 1 1 0 0 1 1 1V20a1 1 0 0 1-1 1A17 17 0 0 1 3 4a1 1 0 0 1 1-1h3.5a1 1 0 0 1 1 1 11.4 11.4 0 0 0 .6 3.6 1 1 0 0 1-.25 1z"/></svg>
    1300 555 042
  </div>
  <div class="item">
    <svg width="16" height="8" viewBox="0 0 16 8"><path d="M2 2l4 4 4-4" stroke="#0a78b5" stroke-width="1.5" fill="none"/></svg>
    <svg width="10" height="10" viewBox="0 0 24 24"><circle cx="12" cy="7" r="5"/><path d="M2 23c0-6 4.5-9 10-9s10 3 10 9z"/></svg>
    My Account
  </div>
  <div class="item">
    <svg width="16" height="8" viewBox="0 0 16 8"><path d="M2 2l4 4 4-4" stroke="#0a78b5" stroke-width="1.5" fill="none"/></svg>
    <svg width="11" height="10" viewBox="0 0 24 22"><path d="M0 1h4l3 12h13l3-9H7" stroke="#0a78b5" stroke-width="2.5" fill="none"/><circle cx="9" cy="19" r="2"/><circle cx="19" cy="19" r="2"/></svg>
    My Cart
  </div>
  <div class="social"><span></span><span></span><span></span></div>
</div>

<header class="abs header"></header>
<div class="abs logo"><i></i>BRTL</div>
<nav class="abs nav">
  <a>Home</a>
  <a class="boxed">About Us ⊕</a>
  <a>Services</a>
  <a class="boxed">Commercial</a>
  <a>ISP</a>
  <a>Recent Projects</a>
  <a>Contact Us</a>
</nav>

<section class="abs hero" role="img" aria-label="Close-up photo of a technician splicing fibre optic cables with a fusion splicer"></section>
<div class="abs hero-shadow"></div>
<div class="abs dropdown">
  <div>ITEM-1</div>
  <div>ITEM-2</div>
  <div class="on">ITEM-3</div>
</div>
<div class="abs caption">
  <h1>BRTL Is A Communications Intergration Company</h1>
  <p>Incorporating The Expertise Of Data And Fibre Optic Communication,<br>ICT And Low Voltage System, Security And Application Services.</p>
</div>
<div class="abs btn-light read-more">READ MORE</div>
<div class="abs arrow" style="left:70px"><svg width="26" height="16" viewBox="0 0 26 16"><path d="M25 8H3M9 2L3 8l6 6" stroke="#fff" stroke-width="3" fill="none"/></svg></div>
<div class="abs arrow" style="left:1077px"><svg width="26" height="16" viewBox="0 0 26 16"><path d="M1 8h22M17 2l6 6-6 6" stroke="#fff" stroke-width="3" fill="none"/></svg></div>

<!-- About -->
<h2 class="abs title" style="top:600px"><span class="rule l"></span>About Us<span class="rule r"></span></h2>
<div class="abs about-photo" role="img" aria-label="Photo of glowing blue fibre optic strands"></div>
<div class="abs about-text">
  <p>BRTL is a Communications Integration Company incorporating the expertise of Data and Fibre Optic Communications, ICT and low voltage systems, Security and Application Services. with over five decades of experience and successes in their respected field of expertise. The quality and proven ability of our management and tradespeople, in conjunction with our extensive network of resources, ensures a successful outcome for our clients.</p>
  <p>At BRTL our mission is to maximise the value of the service offered to our clients and perform these services through a well-managed process, focusing on quality, technical reliability and cost effectiveness.It is our commitment to provide service with the highest professional standard of excellence, integrity and efficiency.</p>
  <p>BRTL is able to provide a unique level of knowledge and experience to address the issues associated with all projects. We have extensive experience in many types of installations across a wide variety of environments, which provides us with skills in identifying problems early providing resolutions, which allows us to deliver a successful outcome.</p>
</div>
<div class="abs btn-blue learn-more">LEARN MORE</div>

<!-- Services -->
<section class="abs services"></section>
<h2 class="abs title on-blue" style="top:962px"><span class="rule l"></span>Our Services<span class="rule r"></span></h2>
<div class="abs service" style="left:132px">
  <div class="disc" role="img" aria-label="Photo of blue fibre optic light strands" style="background:radial-gradient(circle,#7fdcff 0%,#1592d2 45%,#053e7a 100%)">
    <svg width="42" height="42" viewBox="0 0 42 42"><circle cx="21" cy="21" r="21" fill="#fff"/><circle cx="19" cy="19" r="7" stroke="#0a78b5" stroke-width="3" fill="none"/><path d="M24 24l6 6" stroke="#0a78b5" stroke-width="3.5"/></svg>
  </div>
  <h3>Fibre Optics</h3>
  <p>BRTL has highly trained and proficient engineers, technicians and project managers to ensure that we deliver every fibre project to specification.</p>
</div>
<div class="abs service" style="left:378px">
  <div class="disc" role="img" aria-label="Photo of a CCTV camera in front of office towers" style="background:linear-gradient(135deg,#cfe0ec 0%,#7fa3bd 50%,#3a5468 100%)"></div>
  <h3>Security</h3>
  <p>The BRTL range of IP CCTV cameras and platforms allows you to keep current with technology advancements across every site you manage.</p>
</div>
<div class="abs service" style="left:623px">
  <div class="disc" role="img" aria-label="Photo of technicians working on a rooftop above a city skyline" style="background:linear-gradient(180deg,#9cc4e4 0%,#6c7f8c 55%,#3c4a52 100%)"></div>
  <h3>Building Services</h3>
  <p>BRTL has highly trained and proficient engineers, technicians and project managers to ensure that we meet every building requirement.</p>
</div>
<div class="abs service" style="left:868px">
  <div class="disc" role="img" aria-label="Photo of orange electrical switchboard cabinets" style="background:linear-gradient(135deg,#f08a3a 0%,#d85a10 60%,#8a3206 100%)"></div>
  <h3>Electrical</h3>
  <p>BRTL carries out the design, installation, commissioning and maintenance of a wide range of electrical systems for commercial sites.</p>
</div>

<!-- Projects -->
<h2 class="abs title" style="top:1369px"><span class="rule l"></span>Our Projects<span class="rule r"></span></h2>
<div class="abs filters">
  <span class="on" style="width:53px">All</span>
  <span style="width:147px">Current Projects</span>
  <span style="width:132px">Past Projects</span>
</div>

<article class="abs project" style="left:125px">
  <div class="shot" role="img" aria-label="Aerial photo of a green residential development site" style="background:linear-gradient(135deg,#8fb27a,#5f8a58)">
    <div class="overlay"><svg width="34" height="34" viewBox="0 0 34 34"><circle cx="14" cy="14" r="11" stroke="#fff" stroke-width="3" fill="none"/><path d="M22 22l9 9M14 8v12M8 14h12" stroke="#fff" stroke-width="3"/></svg></div>
  </div>
  <h3>Harlow Ridge Telecommunications Backhaul</h3>
  <p>The installation of Fibre optic back haul for Harlow Ridge New development ‘Verda’ http://www.verdaharlow.com.au/masterplan<br>The installation of 4.0 kilometres of telecommunications pit and pipe infrastructure from Milford Road through</p>
</article>
<article class="abs project" style="left:451px">
  <div class="shot" role="img" aria-label="Photo of two residential towers covered in vertical gardens" style="background:linear-gradient(180deg,#dfe9ef 0%,#b7a77a 55%,#6b7a4e 100%)"></div>
  <h3>Park Quarter Tower</h3>
  <p>Bayside Central Park occupies nearly six hectares of the southern Bayside CBD, defining Bayside’s ‘downtown’. Central Park is the kestrels-1.jpgvisionary redevelopment of the old Old Foundry Works site, bordered by Grand and Elm Streets in Eastbrook.</p>
</article>
<article class="abs project" style="left:776px">
  <div class="shot" role="img" aria-label="Aerial rendering of a master-planned residential estate" style="background:linear-gradient(135deg,#a7c08c,#6d9163 60%,#8fa7a0)"></div>
  <h3>Harlow Ridge Telecommunications Backhaul</h3>
  <p>The installation of Fibre optic back haul for Harlow Ridge New development ‘Verda’ http://www.verdaharlow.com.au/masterplan<br>The installation of 4.0 kilometres of telecommunications pit and pipe infrastructure from Milford Road through</p>
</article>

<!-- Footer -->
<footer class="abs footer">
  <h4 style="left:15px">Contact BRTL</h4>
  <div class="contact-note">Please contact us on 1300 555 042 or fill out below</div>
  <div class="field" style="left:16px;top:94px;width:142px;height:28px">First Name</div>
  <div class="field" style="left:162px;top:94px;width:137px;height:28px">Last Name</div>
  <div class="field" style="left:16px;top:126px;width:283px;height:28px">Email Address</div>
  <div class="field" style="left:16px;top:158px;width:283px;height:28px">Primary Contact Phone</div>
  <div class="field" style="left:16px;top:190px;width:283px;height:94px">How can we help you today?</div>
  <div class="btn-light submit">SUBMIT</div>

  <h4 style="left:325px">My Account</h4>
  <div class="links" style="left:325px">
    <div>My Account</div><div>Sign In</div><div>Order Status</div><div>My Cart</div><div>My Wishlist</div>
  </div>

  <h4 style="left:489px">Information</h4>
  <div class="links wide" style="left:489px">
    <div>About Us</div><div>Services</div><div>ISP</div><div>Recent Projects</div><div>Contact Us</div><div>Blog</div>
  </div>

  <h4 style="left:729px">Latest Tweets</h4>
  <div class="tweets">
    <div class="tweet"><i></i><div>Nimbus has now a Tessera version - http://t.co/Kx4PLmw2Qa<small>01:53 AM Dec 19th</small></div></div>
    <div class="tweet"><i></i><div>Nimbus has now a Tessera version - http://t.co/Kx4PLmw2Qa<small>01:53 AM Dec 19th</small></div></div>
    <div class="tweet"><i></i><div>Nimbus has now a Tessera version - http://t.co/Kx4PLmw2Qa<small>01:53 AM Dec 19th</small></div></div>
  </div>

  <div class="footer-rule"></div>
  <div class="copyright">Copyright 2015 BRTL Group. All Rights Reserved. Sitemap</div>
</footer>

</body>
</html>
```